Creation of brand identity and website "Tandem K"

I am currently seeking an brand, identity and web design for a new project called Tandem K. This is a brand new concept from scratch and you have free-reign on the whole design process, taking into account my preference below.

Must include the name "Tandem K", or "Tandem K: Or the year I woke Up". Kudos is this forms part of the brands logo

Design that can be easily scaled to potentially include: a blog, timeline and vlogs.

Minimal but effective use of colour (however any colours and combinations permitted

Use of icons/graphics over text wherever possible

Minimal use of frames and borders

I appreciate this is a fairly wide scope so please contact me on marblefinch@postwillow.com with any questions or more information on what the project is.

Target Market(s)

Male and Female 20-40
Blog readers
Selfhelp

Industry/Entity Type

Seeking

Number of Pages Required

1 page

Font styles to use
Serif
Sans Serif

Requirements
Must have
• It is in effect a blog design, so about me section, recent blog / archived posts, reader comments / Q and A section.
• A coded design would be appreciated to make my life easier however I have left the design as uncoded as getting the right design matters more to me and I want to keep the project open to as many designers as possible
Nice to have
• See project description for other details and please ask if you need anything else :)
Should not have
• Mustn't be cluttered or feel fussy
• Promote icons over text
• Frames / multiple borders

```html
<!DOCTYPE html>
<html lang="en">
<head>
<meta charset="utf-8">
<title>Tandem K — Blog</title>
<link href="https://fonts.googleapis.com/css2?family=Alegreya+Sans+SC:wght@700&family=Lato:wght@300;400;700;900&display=swap" rel="stylesheet">
<style>
:root{
  --blue:#0a86c4;
  --blue-dark:#066a9c;
  --ink:#222;
  --text:#5b5b5b;
  --muted:#8c8c8c;
  --page:#efefef;
  --card:#fff;
  --line:#e6e6e6;
  --foot:#1f1f1f;
  --soft:#dcedf5;
}
*{box-sizing:border-box;margin:0;padding:0}
html,body{width:1200px;height:2736px;overflow:hidden}
body{background:var(--page);font-family:"Lato",sans-serif;color:var(--text);position:relative}

/* header */
.site-header{position:absolute;top:0;left:0;width:1200px;height:82px;background:#f6f6f6;border-top:3px solid var(--blue)}
.brand{position:absolute;left:100px;top:22px;display:flex;align-items:center;gap:12px;font-weight:900;font-size:34px;letter-spacing:1px;color:var(--ink);text-transform:uppercase}
.brand-mark{width:26px;height:26px;background:var(--blue)}
.social-tab{position:absolute;left:857px;top:0;width:237px;height:33px;background:var(--blue);clip-path:polygon(0 0,100% 0,92% 100%,8% 100%);display:flex;justify-content:center;align-items:center;gap:14px}
.dot{width:13px;height:13px;border-radius:50%;background:#fff;display:block}
.main-nav{position:absolute;right:98px;top:50px;display:flex;gap:42px;font-size:15px;font-weight:400;color:var(--ink);text-transform:uppercase}
.main-nav .active{color:var(--blue)}

/* hero */
.hero{position:absolute;top:82px;left:0;width:1200px;height:387px;background:linear-gradient(180deg,#d9cfb8 0%,#b9b4a6 35%,#6d6c66 70%,#3f3e3b 100%)}
.hero-title{position:absolute;top:180px;width:100%;text-align:center;font-family:"Alegreya Sans SC",sans-serif;font-weight:700;font-size:44px;line-height:52px;color:#fff;letter-spacing:2px;text-shadow:0 2px 6px rgba(0,0,0,.4)}
.hero-dots{position:absolute;top:436px;left:555px;display:flex;gap:6px}
.hero-dots span{width:26px;height:5px;background:#fff;opacity:.7}
.hero-dots .on{background:var(--blue);opacity:1}

/* posts */
.posts{position:absolute;left:100px;top:494px;width:657px}
.post{background:var(--card);height:640px;margin-bottom:32px;position:relative}
.post-head{height:101px;position:relative}
.date-badge{position:absolute;left:15px;top:15px;width:55px;text-align:center}
.date-badge .day{display:block;background:var(--blue);color:#fff;font-weight:700;font-size:21px;height:34px;line-height:34px}
.date-badge .month{display:block;background:#111;color:#fff;font-size:12px;font-weight:700;line-height:14px;padding:4px 0}
.post-title{position:absolute;left:92px;top:22px;font-size:22px;font-weight:700;color:var(--ink)}
.post-author{position:absolute;left:92px;top:60px;font-size:13px;font-weight:700;color:#333;display:flex;align-items:center;gap:7px}
.share-btn{position:absolute;right:22px;top:20px;width:112px;height:42px;background:var(--blue);color:#fff;font-size:16px;display:flex;align-items:center;justify-content:center;gap:8px;clip-path:polygon(0 4%,100% 0,98% 100%,2% 96%)}
.post-photo{height:311px}
.photo-tree{background:linear-gradient(180deg,#8d9398 0%,#c4c8c9 45%,#79a03c 75%,#8c8476 100%)}
.photo-lake{background:linear-gradient(180deg,#c9dbe9 0%,#8fa86f 40%,#8ea6b3 60%,#bdb3a2 100%)}
.photo-shore{background:linear-gradient(180deg,#5f4b44 0%,#d8c6a6 45%,#7c6a61 70%,#3c3434 100%)}
.post-body{padding:14px 16px 0}
.post-excerpt{font-size:12.6px;line-height:21.5px;color:var(--text)}
.read-more{display:inline-block;margin-top:15px;background:var(--blue);color:#fff;font-size:14px;font-weight:700;height:33px;line-height:33px;padding:0 17px;border-radius:2px}
.post-foot{position:absolute;left:0;bottom:0;width:657px;height:60px;border-top:1px solid var(--line);display:flex;align-items:center}
.pin{margin-left:15px;width:38px;height:38px;border:2px solid var(--blue);border-radius:50%;display:flex;align-items:center;justify-content:center}
.reply-btn{margin-left:22px;background:var(--blue);color:#fff;font-size:13.5px;font-weight:700;height:33px;line-height:33px;padding:0 16px;border-radius:2px}
.meta{margin-left:16px;font-size:13.5px;color:#444;display:flex;align-items:center;gap:7px}
.meta + .meta{margin-left:0;padding-left:16px;border-left:1px solid var(--line)}
.foot-tools{margin-left:auto;width:168px;height:100%;background:#e3e3e3;display:flex;align-items:center;justify-content:center;gap:22px;font-size:13.5px;color:#555}
.foot-tools span{display:flex;align-items:center;gap:7px}

.pager{background:var(--card);height:69px;display:flex;align-items:center;justify-content:center;gap:6px;font-size:14px;color:#333}
.pager b{display:inline-block;min-width:22px;height:18px;line-height:18px;background:var(--blue);color:#fff;font-weight:400;font-size:12px;text-align:center;padding:0 4px}
.pager .nav-link{margin:0 8px}

/* sidebar */
.sidebar{position:absolute;left:788px;top:494px;width:314px}
.widget{background:var(--card);margin-bottom:28px;padding:18px 16px}
.widget-label{font-size:14px;color:#333;text-transform:uppercase}
.search-field{margin-top:14px;height:33px;background:#ececec;font-size:12px;color:#888;padding-left:28px;line-height:33px;position:relative}
.search-field svg{position:absolute;left:10px;top:11px}

.about{padding:0;position:relative;height:320px}
.about-cover{height:161px;background:linear-gradient(135deg,#0b6fa6 0%,#1a90cc 50%,#0a5f8f 100%)}
.avatar{position:absolute;left:97px;top:-4px;width:120px;height:120px;border-radius:50%;border:4px solid #fff;background:linear-gradient(180deg,#dde6ea,#9fb6c3)}
.about-name{position:absolute;top:118px;width:100%;text-align:center;font-size:32px;font-weight:400;color:#fff}
.about-text{padding:14px 18px 0;font-size:12.5px;line-height:21px;color:var(--text)}
.about-text p + p{margin-top:10px}
.contact-ribbon{position:absolute;left:10px;bottom:0;width:294px;height:40px;background:var(--blue);clip-path:polygon(0 0,100% 0,96% 100%,4% 100%);display:flex;align-items:center;justify-content:center;gap:8px;color:#fff;font-weight:700;font-size:15px}
.contact-ribbon .ring{width:24px;height:24px;border-radius:50%;background:#fff}
.contact-ribbon .label{margin-right:4px}

.tabs{display:flex;gap:0;font-size:14px;color:#333;text-transform:uppercase;border-bottom:1px solid var(--line);margin-bottom:10px}
.tabs span{padding-bottom:8px}
.tabs .current{border-bottom:3px solid var(--blue)}
.tabs .sep{margin:0 14px;color:#bbb}
.thumb-list li{list-style:none;display:flex;gap:10px;height:68px;align-items:flex-start}
.thumb{width:48px;height:48px;flex:none;margin-top:6px}
.t1{background:linear-gradient(135deg,#2f4e5e,#c9b690)}
.t2{background:linear-gradient(135deg,#e6d9c1,#3b3129)}
.t3{background:linear-gradient(135deg,#8cc0da,#5e8a3d)}
.t4{background:linear-gradient(135deg,#a9d0e8,#3f6f91)}
.t5{background:linear-gradient(135deg,#bcd6a4,#e1e6e9)}
.t6{background:linear-gradient(135deg,#e0b040,#c55d1f)}
.t7{background:linear-gradient(135deg,#1b2a42,#6d89a7)}
.t8{background:linear-gradient(135deg,#9fc7e4,#c4553a)}
.thumb-text{font-size:12px;line-height:16px;margin-top:6px}
.thumb-text strong{display:block;font-weight:400;color:#222;font-size:12.5px}
.thumb-text .date{color:var(--muted);font-size:11.5px;display:flex;align-items:center;gap:6px;margin-top:2px}

.cat-list li{list-style:none;height:36px;display:flex;align-items:center;font-size:12.5px;color:#444;border-bottom:1px solid #eee;padding:0 4px}
.cat-list li::before{content:"";width:0;height:0;border-left:5px solid var(--blue);border-top:4px solid transparent;border-bottom:4px solid transparent;margin-right:12px}
.cat-list li span{margin-left:auto;color:var(--muted)}
.cat-list li.hl{background:var(--soft)}
.cat-list li:last-child{border-bottom:none}

.comments li{height:69px}

/* footer */
.site-footer{position:absolute;left:0;top:2610px;width:1200px;height:82px;background:var(--foot)}
.newsletter{position:absolute;left:98px;top:25px;display:flex;align-items:center;gap:10px;color:#fff;font-size:19px}
.news-input{margin-left:6px;width:217px;height:28px;background:#fff;font-size:12px;color:#777;line-height:28px;padding-left:8px}
.news-btn{margin-left:-10px;height:28px;line-height:28px;background:var(--blue);color:#fff;font-size:12.5px;font-weight:700;padding:0 10px}
.get-in-touch{position:absolute;right:98px;top:31px;display:flex;align-items:center;gap:18px;color:#ddd;font-size:13px}
.get-in-touch .dot{background:#fff}
.get-in-touch .dot.first{background:var(--blue)}
.copyright{position:absolute;left:0;top:2692px;width:1200px;height:44px;background:var(--blue);color:#fff;font-size:13px;text-align:center;line-height:44px}
</style>
</head>
<body>

<header class="site-header">
  <div class="brand"><span>Tandem K</span><span class="brand-mark"></span></div>
  <div class="social-tab"><i class="dot"></i><i class="dot"></i><i class="dot"></i><i class="dot"></i><i class="dot"></i><i class="dot"></i></div>
  <nav class="main-nav"><span class="active">Home</span><span>About Us</span><span>Contact Us</span></nav>
</header>

<section class="hero" role="img" aria-label="City skyline photograph at sunrise">
  <h1 class="hero-title">I changed my thinking.<br>It changed my life.</h1>
</section>
<div class="hero-dots"><span></span><span class="on"></span><span></span></div>

<main class="posts">
  <article class="post">
    <div class="post-head">
      <div class="date-badge"><span class="day">02</span><span class="month">Apr<br>2016</span></div>
      <h2 class="post-title">Lorem ipsum dolor sit amet, consectetuer...</h2>
      <div class="post-author"><svg width="11" height="12" viewBox="0 0 11 12"><circle cx="5.5" cy="3.5" r="3" fill="#666"/><path d="M0 12c0-4 2.5-5 5.5-5s5.5 1 5.5 5z" fill="#666"/></svg>Wes Harlow</div>
      <div class="share-btn"><svg width="14" height="14" viewBox="0 0 14 14"><circle cx="11" cy="3" r="2.5" fill="#fff"/><circle cx="3" cy="7" r="2.5" fill="#fff"/><circle cx="11" cy="11" r="2.5" fill="#fff"/><path d="M11 3 3 7l8 4" stroke="#fff" stroke-width="1.4" fill="none"/></svg>Share It</div>
    </div>
    <div class="post-photo photo-tree" role="img" aria-label="Photograph of a lone tree between cracked dry earth and green grass under a stormy sky"></div>
    <div class="post-body">
      <p class="post-excerpt">Lorem Ipsum is simply dummy text of the printing and typesetting industry. Lorem Ipsum has been the industry's standard dummy text ever since the 1500s, when an unknown printer took a galley of type and scrambled it to make a type specimen book. It has survived not only five centuries, but also the leap into electronic typesetting, remaining essentially unchanged. It was popularised in the 1960s with the release of Letraset she.</p>
      <span class="read-more">Read More</span>
    </div>
    <div class="post-foot">
      <span class="pin"><svg width="14" height="16" viewBox="0 0 14 16"><path d="M3 1h8l-1.5 2v4L12 10H2l2.5-3V3z" fill="#0a86c4"/><path d="M7 10v6" stroke="#0a86c4" stroke-width="1.6"/></svg></span>
      <span class="reply-btn">Leave a Reply</span>
      <span class="meta"><svg width="14" height="12" viewBox="0 0 14 12"><path d="M1 1h12v7H6l-3 3V8H1z" fill="none" stroke="#555" stroke-width="1.3"/></svg>Comments : 0</span>
      <span class="meta"><svg width="15" height="10" viewBox="0 0 15 10"><path d="M.5 5C3 0 12 0 14.5 5 12 10 3 10 .5 5z" fill="#555"/><circle cx="7.5" cy="5" r="2" fill="#fff"/></svg>200</span>
      <div class="foot-tools">
        <span><svg width="14" height="13" viewBox="0 0 14 13"><rect x="3" y="0" width="8" height="4" fill="#666"/><rect x="0" y="4" width="14" height="6" fill="#666"/><rect x="3" y="8" width="8" height="5" fill="#fff" stroke="#666"/></svg>Print</span>
        <span><svg width="11" height="14" viewBox="0 0 11 14"><path d="M.5.5h7l3 3v10H.5z" fill="none" stroke="#666"/></svg>Pdf</span>
      </div>
    </div>
  </article>

  <article class="post">
    <div class="post-head">
      <div class="date-badge"><span class="day">02</span><span class="month">Apr<br>2016</span></div>
      <h2 class="post-title">Lorem ipsum dolor sit amet, consectetuer...</h2>
      <div class="post-author"><svg width="11" height="12" viewBox="0 0 11 12"><circle cx="5.5" cy="3.5" r="3" fill="#666"/><path d="M0 12c0-4 2.5-5 5.5-5s5.5 1 5.5 5z" fill="#666"/></svg>Wes Harlow</div>
      <div class="share-btn"><svg width="14" height="14" viewBox="0 0 14 14"><circle cx="11" cy="3" r="2.5" fill="#fff"/><circle cx="3" cy="7" r="2.5" fill="#fff"/><circle cx="11" cy="11" r="2.5" fill="#fff"/><path d="M11 3 3 7l8 4" stroke="#fff" stroke-width="1.4" fill="none"/></svg>Share It</div>
    </div>
    <div class="post-photo photo-lake" role="img" aria-label="Photograph of a person in a sun hat sitting on a wooden pier facing a mountain lake"></div>
    <div class="post-body">
      <p class="post-excerpt">Lorem Ipsum is simply dummy text of the printing and typesetting industry. Lorem Ipsum has been the industry's standard dummy text ever since the 1500s, when an unknown printer took a galley of type and scrambled it to make a type specimen book. It has survived not only five centuries, but also the leap into electronic typesetting, remaining essentially unchanged. It was popularised in the 1960s with the release of Letraset she.</p>
      <span class="read-more">Read More</span>
    </div>
    <div class="post-foot">
      <span class="pin"><svg width="14" height="16" viewBox="0 0 14 16"><path d="M3 1h8l-1.5 2v4L12 10H2l2.5-3V3z" fill="#0a86c4"/><path d="M7 10v6" stroke="#0a86c4" stroke-width="1.6"/></svg></span>
      <span class="reply-btn">Leave a Reply</span>
      <span class="meta"><svg width="14" height="12" viewBox="0 0 14 12"><path d="M1 1h12v7H6l-3 3V8H1z" fill="none" stroke="#555" stroke-width="1.3"/></svg>Comments : 0</span>
      <span class="meta"><svg width="15" height="10" viewBox="0 0 15 10"><path d="M.5 5C3 0 12 0 14.5 5 12 10 3 10 .5 5z" fill="#555"/><circle cx="7.5" cy="5" r="2" fill="#fff"/></svg>200</span>
      <div class="foot-tools">
        <span><svg width="14" height="13" viewBox="0 0 14 13"><rect x="3" y="0" width="8" height="4" fill="#666"/><rect x="0" y="4" width="14" height="6" fill="#666"/><rect x="3" y="8" width="8" height="5" fill="#fff" stroke="#666"/></svg>Print</span>
        <span><svg width="11" height="14" viewBox="0 0 11 14"><path d="M.5.5h7l3 3v10H.5z" fill="none" stroke="#666"/></svg>Pdf</span>
      </div>
    </div>
  </article>

  <article class="post">
    <div class="post-head">
      <div class="date-badge"><span class="day">02</span><span class="month">Apr<br>2016</span></div>
      <h2 class="post-title">Lorem ipsum dolor sit amet, consectetuer...</h2>
      <div class="post-author"><svg width="11" height="12" viewBox="0 0 11 12"><circle cx="5.5" cy="3.5" r="3" fill="#666"/><path d="M0 12c0-4 2.5-5 5.5-5s5.5 1 5.5 5z" fill="#666"/></svg>Wes Harlow</div>
      <div class="share-btn"><svg width="14" height="14" viewBox="0 0 14 14"><circle cx="11" cy="3" r="2.5" fill="#fff"/><circle cx="3" cy="7" r="2.5" fill="#fff"/><circle cx="11" cy="11" r="2.5" fill="#fff"/><path d="M11 3 3 7l8 4" stroke="#fff" stroke-width="1.4" fill="none"/></svg>Share It</div>
    </div>
    <div class="post-photo photo-shore" role="img" aria-label="Photograph of a silhouetted person with open arms on a pebble shore at sunset"></div>
    <div class="post-body">
      <p class="post-excerpt">Lorem Ipsum is simply dummy text of the printing and typesetting industry. Lorem Ipsum has been the industry's standard dummy text ever since the 1500s, when an unknown printer took a galley of type and scrambled it to make a type specimen book. It has survived not only five centuries, but also the leap into electronic typesetting, remaining essentially unchanged. It was popularised in the 1960s with the release of Letraset she.</p>
      <span class="read-more">Read More</span>
    </div>
    <div class="post-foot">
      <span class="pin"><svg width="14" height="16" viewBox="0 0 14 16"><path d="M3 1h8l-1.5 2v4L12 10H2l2.5-3V3z" fill="#0a86c4"/><path d="M7 10v6" stroke="#0a86c4" stroke-width="1.6"/></svg></span>
      <span class="reply-btn">Leave a Reply</span>
      <span class="meta"><svg width="14" height="12" viewBox="0 0 14 12"><path d="M1 1h12v7H6l-3 3V8H1z" fill="none" stroke="#555" stroke-width="1.3"/></svg>Comments : 0</span>
      <span class="meta"><svg width="15" height="10" viewBox="0 0 15 10"><path d="M.5 5C3 0 12 0 14.5 5 12 10 3 10 .5 5z" fill="#555"/><circle cx="7.5" cy="5" r="2" fill="#fff"/></svg>200</span>
      <div class="foot-tools">
        <span><svg width="14" height="13" viewBox="0 0 14 13"><rect x="3" y="0" width="8" height="4" fill="#666"/><rect x="0" y="4" width="14" height="6" fill="#666"/><rect x="3" y="8" width="8" height="5" fill="#fff" stroke="#666"/></svg>Print</span>
        <span><svg width="11" height="14" viewBox="0 0 11 14"><path d="M.5.5h7l3 3v10H.5z" fill="none" stroke="#666"/></svg>Pdf</span>
      </div>
    </div>
  </article>

  <nav class="pager">
    <span class="nav-link">« Prview</span>
    <b>1</b><b>2</b><b>3</b><b>…</b><b>19</b><b>20</b>
    <span class="nav-link">Next »</span>
  </nav>
</main>

<aside class="sidebar">
  <section class="widget" style="height:95px;padding-top:16px">
    <div class="widget-label">Search</div>
    <div class="search-field"><svg width="11" height="11" viewBox="0 0 11 11"><circle cx="4.5" cy="4.5" r="3.5" fill="none" stroke="#888" stroke-width="1.4"/><path d="M7 7l3.5 3.5" stroke="#888" stroke-width="1.4"/></svg>Search Now !</div>
  </section>

  <section class="widget about" style="margin-top:-25px;margin-bottom:29px">
    <div class="about-cover" role="img" aria-label="Blue low-poly geometric background"></div>
    <div class="avatar" role="img" aria-label="Portrait of the author" style="top:8px"></div>
    <div class="about-name">Wes Harlow</div>
    <div class="about-text">
      <p>"Neque porro quisquam est qui dolorem ipsum quia dolor sit amet, consectetur, adipisci veli...</p>
      <p>There is no one who loves pain itself, who seeks after it and wants to have it, simply because[+]</p>
    </div>
    <div class="contact-ribbon"><span class="label">Contact Me</span><i class="ring"></i><i class="ring"></i><i class="ring"></i><i class="ring"></i></div>
  </section>

  <section class="widget" style="height:342px;padding-top:16px">
    <div class="tabs"><span class="current">Recent Post</span><span class="sep">|</span><span>Popular Post</span></div>
    <ul class="thumb-list">
      <li><span class="thumb t1" role="img" aria-label="Post thumbnail"></span><div class="thumb-text"><strong>Duis sagittis libero eu urna te</strong>Possibility to pin websites to your<span class="date">▢ July 31, 2015</span></div></li>
      <li><span class="thumb t2" role="img" aria-label="Post thumbnail"></span><div class="thumb-text"><strong>Duis interdum odio in nunc 0..</strong>Possibility to pin websites to your<span class="date">▢ July 24, 2015</span></div></li>
      <li><span class="thumb t3" role="img" aria-label="Post thumbnail"></span><div class="thumb-text"><strong>In dictum nulla at nisl dapibus...</strong>Possibility to pin websites to your<span class="date">▢ July 17, 2015</span></div></li>
      <li><span class="thumb t4" role="img" aria-label="Post thumbnail"></span><div class="thumb-text"><strong>Quisque porta turpis in nunc semper...</strong>Possibility to pin websites to your<span class="date">▢ July 11, 2015</span></div></li>
    </ul>
  </section>

  <section class="widget" style="height:460px;padding-top:16px">
    <div class="tabs"><span class="current">Categories</span><span class="sep">|</span><span>Tags</span></div>
    <ul class="cat-list">
      <li>Lorem ipsum<span>(8)</span></li>
      <li>Maecenas<span>(28)</span></li>
      <li>Phasellus nec<span>(4)</span></li>
      <li class="hl">magna acjusto<span>(1)</span></li>
      <li>tempor pretium<span>(2)</span></li>
      <li>turpis<span>(1)</span></li>
      <li>Nam eget<span>(1)</span></li>
      <li>justo tincidunt<span>(5)</span></li>
      <li>ullamcorper<span>(1)</span></li>
      <li>Etiam euismo<span>(1)</span></li>
      <li>volutpat<span>(1)</span></li>
    </ul>
  </section>

  <section class="widget" style="height:328px;padding-top:16px">
    <div class="widget-label" style="margin-bottom:4px">Comments</div>
    <ul class="thumb-list comments">
      <li><span class="thumb t5" role="img" aria-label="Commenter thumbnail"></span><div class="thumb-text"><strong>Lorem ipsum dolor</strong>Lorem Ipsum is simply dummy text of the printing and typesetting industry.</div></li>
      <li><span class="thumb t6" role="img" aria-label="Commenter thumbnail"></span><div class="thumb-text"><strong>Maecenas efficitur quam</strong>Lorem Ipsum is simply dummy text of the printing and typesetting industry.</div></li>
      <li><span class="thumb t7" role="img" aria-label="Commenter thumbnail"></span><div class="thumb-text"><strong>Nam eget nisi nec justo</strong>Lorem Ipsum is simply dummy text of the printing and typesetting industry.</div></li>
      <li><span class="thumb t8" role="img" aria-label="Commenter thumbnail"></span><div class="thumb-text"><strong>Fusce hendrerit metus</strong>Lorem Ipsum is simply dummy text of the printing and typesetting industry.</div></li>
    </ul>
  </section>
</aside>

<footer class="site-footer">
  <div class="newsletter">
    <svg width="26" height="24" viewBox="0 0 26 24"><path d="M1 10 13 1l12 9v13H1z" fill="#fff"/><path d="M1 10l12 8 12-8" fill="none" stroke="#1f1f1f" stroke-width="1.6"/></svg>
    <span>Newsletter Signup</span>
    <span class="news-input">✉ Enter your email here</span>
    <span class="news-btn">SUBSCRIBE</span>
  </div>
  <div class="get-in-touch"><span>Get in Touch :</span><i class="dot first"></i><i class="dot"></i><i class="dot"></i><i class="dot"></i><i class="dot"></i><i class="dot"></i></div>
</footer>
<div class="copyright">Copyright © 2016 TandemK. All Rights Reserved.</div>

</body>
</html>
```